Theme and starter template for small business powerpoint deck

We are starting a technology consulting company and would like to have a powerpoint/google slide theme and initial template. We are more concerned with the theme/colors at this point. Initial template can be pretty simple. We would want a cover slide, agenda slide, some content slides including text content, image content, a combination of both, etc. A closing slide. we have included jpg files of our logo, let us know if you would prefer eps/vector. I assume you may want exact color data as well?

Target Market(s)

Technology and Customer Experience Leadership at companies with 25 or more employees

Industry/Entity Type

Technology Consulting

Font styles to use
Sans Serif

Colors
0054AA
0677BA
7BADD7
CADEEF
E8F1F8

Requirements
Must have
• I have attached JPG and EPS and vector files to project. I would like to stay with those colors but open to slight variation if recommended.

```html
<!DOCTYPE html>
<html lang="en">
<head>
<meta charset="utf-8">
<title>Veltrion – Technology Consulting Deck Theme</title>
<link href="https://fonts.googleapis.com/css2?family=Poppins:wght@400;500;600;700&family=Questrial&display=swap" rel="stylesheet">
<style>
:root{
  --navy:#0054AA;
  --blue:#0677BA;
  --sky:#7BADD7;
  --mist:#CADEEF;
  --ice:#E8F1F8;
  --ink:#1f1f1f;
  --text:#333;
  --canvas:#000;
  --white:#fff;
}
*{box-sizing:border-box;margin:0;padding:0}
html,body{width:997px;height:1200px;overflow:hidden;background:var(--canvas)}
body{position:relative;font-family:"Questrial",sans-serif;color:var(--text)}
.slide{position:absolute;width:745px;height:418px;background:var(--white);overflow:hidden;transform-origin:0 0;transform:scale(0.5705)}
.abs{position:absolute}
.brand{position:absolute;font-family:"Poppins",sans-serif;font-weight:700;color:var(--ink);letter-spacing:1.5px;line-height:1;padding-bottom:4px;border-bottom:3px solid var(--sky)}
.brand-mark{display:inline-block;width:10px;height:10px;background:var(--blue);margin-left:6px;vertical-align:middle}
.title{position:absolute;font-family:"Poppins",sans-serif;font-weight:600;color:var(--ink);letter-spacing:.5px;line-height:1.15}
.title.underlined{padding-bottom:6px;border-bottom:2px solid var(--sky)}
.body{position:absolute;font-size:8.6px;line-height:1.55;color:var(--text)}
.justify{text-align:justify}

/* cover */
.cover-title{left:42px;top:132px;font-size:34px;font-weight:700}
.cover-rule{left:42px;top:232px;width:242px;height:3px;background:var(--sky)}
.cover-sub{left:42px;top:250px;font-size:17px;line-height:1.6;color:var(--ink);letter-spacing:.3px}

/* agenda */
.agenda-item{position:absolute;width:240px;height:40px}
.agenda-item h4{font-family:"Poppins",sans-serif;font-weight:500;font-size:10.5px;color:var(--blue);letter-spacing:.3px}
.agenda-item p{font-size:8.8px;color:var(--text);margin-top:3px}
.agenda-item svg{position:absolute;left:193px;top:-6px}

/* about */
.mission{position:absolute;left:367px;top:246px;width:350px;height:145px;background:var(--blue);color:var(--white);padding:18px 24px}
.mission h4{font-family:"Poppins",sans-serif;font-weight:500;font-size:10px;margin-bottom:9px}
.mission p{font-size:8.6px;line-height:1.55;text-align:justify}

/* services */
.service{position:absolute;top:90px;width:132px}
.service h4{font-family:"Poppins",sans-serif;font-weight:500;font-size:11.5px;color:var(--ink);margin-top:16px;letter-spacing:.3px}
.service p{font-size:7.6px;line-height:1.42;margin-top:8px;height:118px}
.service .bar{height:3px;width:130px;margin-top:10px}

/* tech solutions */
.list-box{position:absolute;top:154px;width:323px;height:240px;border:1px solid #555;padding:18px 14px}
.list-box h4{font-family:"Poppins",sans-serif;font-weight:500;font-size:12px;color:var(--ink);margin-bottom:10px}
.list-box li{list-style:none;font-size:8.4px;line-height:18.7px;position:relative;padding-left:9px;white-space:nowrap}
.list-box li::before{content:"";position:absolute;left:0;top:6px;border-left:4px solid #555;border-top:3px solid transparent;border-bottom:3px solid transparent}

/* infodata */
.info{position:absolute;width:120px;text-align:center}
.info h4{font-family:"Poppins",sans-serif;font-weight:600;font-size:9px;color:var(--blue);letter-spacing:.3px}
.info .tick{width:10px;height:2px;background:var(--blue);margin:3px auto 5px}
.info p{font-size:6.2px;line-height:1.35;color:#777}

/* closing */
.thanks{left:0;width:745px;text-align:center;top:190px;font-family:"Poppins",sans-serif;font-weight:700;font-size:46px;color:var(--blue);letter-spacing:1px}
.contact h4{font-family:"Poppins",sans-serif;font-weight:500;font-size:12px;color:var(--blue);letter-spacing:.3px}
.contact p{font-family:"Poppins",sans-serif;font-weight:500;font-size:12px;color:var(--blue)}
</style>
</head>
<body>

<!-- Cover -->
<section class="slide" style="left:55px;top:67px">
  <svg class="abs" style="left:0;top:0" width="745" height="418" aria-hidden="true">
    <polygon points="590,40 745,310 745,418 430,418" fill="var(--mist)"/>
    <polygon points="470,0 705,418 235,418" fill="var(--navy)"/>
    <polygon points="640,230 745,418 535,418" fill="var(--sky)"/>
  </svg>
  <div class="brand" style="left:42px;top:40px;font-size:31px">VELTRION<span class="brand-mark"></span></div>
  <h1 class="title cover-title">TECHNOLOGY<br>CONSULTING</h1>
  <div class="abs cover-rule"></div>
  <p class="abs cover-sub">INNOVATING TOMORROW'S<br>SOLUTIONS TODAY</p>
</section>

<!-- Agenda -->
<section class="slide" style="left:512px;top:67px">
  <svg class="abs" style="left:0;top:0" width="745" height="418" aria-hidden="true">
    <polygon points="490,0 745,0 612,222" fill="var(--sky)"/>
    <polygon points="745,0 745,418 505,418" fill="var(--navy)"/>
    <line x1="208" y1="0" x2="208" y2="46" stroke="var(--ink)" stroke-width="1.5"/>
  </svg>
  <div class="brand" style="left:22px;top:18px;font-size:20px">VELTRION<span class="brand-mark" style="width:7px;height:7px"></span></div>
  <h2 class="title" style="left:234px;top:16px;font-size:21px;font-weight:500">AGENDA</h2>

  <div class="agenda-item" style="left:21px;top:87px"><h4>LOREM IPSUM</h4><p>Lorem Ipsum is simply dummy text of the</p><svg width="44" height="38"><polygon points="22,0 44,38 0,38" fill="var(--ink)"/><text x="22" y="30" font-size="8" fill="#fff" text-anchor="middle" font-family="Poppins">01</text></svg></div>
  <div class="agenda-item" style="left:21px;top:140px"><h4>LOREM IPSUM</h4><p>Lorem Ipsum is simply dummy text of the</p><svg width="44" height="38"><polygon points="22,0 44,38 0,38" fill="var(--ink)"/><text x="22" y="30" font-size="8" fill="#fff" text-anchor="middle" font-family="Poppins">02</text></svg></div>
  <div class="agenda-item" style="left:21px;top:192px"><h4>LOREM IPSUM</h4><p>Lorem Ipsum is simply dummy text of the</p><svg width="44" height="38"><polygon points="22,0 44,38 0,38" fill="var(--ink)"/><text x="22" y="30" font-size="8" fill="#fff" text-anchor="middle" font-family="Poppins">03</text></svg></div>
  <div class="agenda-item" style="left:21px;top:246px"><h4>LOREM IPSUM</h4><p>Lorem Ipsum is simply dummy text of the</p><svg width="44" height="38"><polygon points="22,0 44,38 0,38" fill="var(--ink)"/><text x="22" y="30" font-size="8" fill="#fff" text-anchor="middle" font-family="Poppins">04</text></svg></div>
  <div class="agenda-item" style="left:21px;top:300px"><h4>LOREM IPSUM</h4><p>Lorem Ipsum is simply dummy text of the</p><svg width="44" height="38"><polygon points="22,0 44,38 0,38" fill="var(--ink)"/><text x="22" y="30" font-size="8" fill="#fff" text-anchor="middle" font-family="Poppins">05</text></svg></div>
  <div class="agenda-item" style="left:21px;top:357px"><h4>LOREM IPSUM</h4><p>Lorem Ipsum is simply dummy text of the</p><svg width="44" height="38"><polygon points="22,0 44,38 0,38" fill="var(--ink)"/><text x="22" y="30" font-size="8" fill="#fff" text-anchor="middle" font-family="Poppins">06</text></svg></div>

  <div class="agenda-item" style="left:301px;top:87px"><h4>LOREM IPSUM</h4><p>Lorem Ipsum is simply dummy text of the</p><svg width="44" height="38"><polygon points="22,0 44,38 0,38" fill="var(--ink)"/><text x="22" y="30" font-size="8" fill="#fff" text-anchor="middle" font-family="Poppins">07</text></svg></div>
  <div class="agenda-item" style="left:301px;top:140px"><h4>LOREM IPSUM</h4><p>Lorem Ipsum is simply dummy text of the</p><svg width="44" height="38"><polygon points="22,0 44,38 0,38" fill="var(--ink)"/><text x="22" y="30" font-size="8" fill="#fff" text-anchor="middle" font-family="Poppins">08</text></svg></div>
  <div class="agenda-item" style="left:301px;top:192px"><h4>LOREM IPSUM</h4><p>Lorem Ipsum is simply dummy text of the</p><svg width="44" height="38"><polygon points="22,0 44,38 0,38" fill="var(--ink)"/><text x="22" y="30" font-size="8" fill="#fff" text-anchor="middle" font-family="Poppins">09</text></svg></div>
  <div class="agenda-item" style="left:301px;top:246px"><h4>LOREM IPSUM</h4><p>Lorem Ipsum is simply dummy text of the</p><svg width="44" height="38"><polygon points="22,0 44,38 0,38" fill="var(--ink)"/><text x="22" y="30" font-size="8" fill="#fff" text-anchor="middle" font-family="Poppins">10</text></svg></div>
  <div class="agenda-item" style="left:301px;top:300px"><h4>LOREM IPSUM</h4><p>Lorem Ipsum is simply dummy text of the</p><svg width="44" height="38"><polygon points="22,0 44,38 0,38" fill="var(--ink)"/><text x="22" y="30" font-size="8" fill="#fff" text-anchor="middle" font-family="Poppins">11</text></svg></div>
  <div class="agenda-item" style="left:301px;top:357px"><h4>LOREM IPSUM</h4><p>Lorem Ipsum is simply dummy text of the</p><svg width="44" height="38"><polygon points="22,0 44,38 0,38" fill="var(--ink)"/><text x="22" y="30" font-size="8" fill="#fff" text-anchor="middle" font-family="Poppins">12</text></svg></div>
</section>

<!-- About us -->
<section class="slide" style="left:55px;top:343px">
  <svg class="abs" style="left:0;top:0" width="360" height="418" role="img" aria-label="Photo of a consulting team gathered around a laptop, tinted blue">
    <defs><linearGradient id="aboutPhoto" x1="0" y1="0" x2="1" y2="1"><stop offset="0" stop-color="#0677BA"/><stop offset="1" stop-color="#003f80"/></linearGradient></defs>
    <polygon points="120,18 355,418 0,418 0,210" fill="url(#aboutPhoto)"/>
  </svg>
  <div class="brand" style="left:170px;top:35px;font-size:21px">VELTRION<span class="brand-mark" style="width:7px;height:7px"></span></div>
  <h2 class="title underlined" style="left:366px;top:30px;font-size:25px">ABOUT US</h2>
  <p class="body justify" style="left:366px;top:92px;width:350px">Sed ut perspiciatis unde omnis iste natus error sit voluptatem accusantium doloremque laudantium, totam rem aperiam, eaque ipsa quae ab illo inventore veritatis et quasi architecto beatae vitae dicta sunt explicabo. Nemo enim ipsam voluptatem quia voluptas sit aspernatur aut odit aut fugit, sed quia consequuntur magni dolores eos qui ratione voluptatem sequi nesciunt. Neque porro quisquam est, qui dolorem ipsum quia dolor sit amet, consectetur, adipisci velit, sed quia non numquam eius modi tempora incidunt ut labore et dolore magnam aliquam quaerat voluptatem. Ut enim ad minima veniam, quis nostrum exercitationem ullam corporis suscipit laboriosam, nisi ut aliquid ex ea commod</p>
  <div class="mission">
    <h4>MISSION</h4>
    <p>Neque porro quisquam est, qui dolorem ipsum quia dolor sit amet, consectetur, adipisci velit, sed quia non numquam eius modi tempora incidunt ut labore et dolore magnam aliquam quaerat voluptatem. Ut enim ad minima veniam, quis nostrum exercitationem ullam corporis suscipit laboriosam, nisi ut aliquid ex ea commodo</p>
  </div>
</section>

<!-- Services -->
<section class="slide" style="left:512px;top:345px">
  <svg class="abs" style="left:0;top:0" width="745" height="418" aria-hidden="true">
    <polygon points="470,0 745,0 745,260" fill="var(--ice)"/>
    <polygon points="0,370 45,418 0,418" fill="var(--ice)"/>
  </svg>
  <div class="brand" style="left:25px;top:22px;font-size:21px">VELTRION<span class="brand-mark" style="width:7px;height:7px"></span></div>
  <h2 class="title underlined" style="left:213px;top:20px;font-size:17px;font-weight:500">SERVICES</h2>

  <div class="service" style="left:33px">
    <svg width="118" height="102" aria-hidden="true"><polygon points="59,0 118,102 0,102" fill="var(--navy)"/>
      <g fill="none" stroke="#fff" stroke-width="2"><rect x="42" y="52" width="14" height="14"/><rect x="58" y="52" width="14" height="14"/><rect x="42" y="68" width="14" height="14"/><rect x="60" y="70" width="14" height="14" fill="#fff"/></g></svg>
    <h4>IT STRATEGY</h4>
    <p>Sed ut perspiciatis unde omnis iste natus error sit voluptatem accusa ntium doloremque laudantium, totam rem aperiam, eaque ipsa quae ab illo inventore veritatis et quasi architecto beatae vitae dicta sunt explicabo. Nemo enim ipsam voluptatem quia voluptas sit aspernatur aut odit aut fugit, sed quia consequuntu.</p>
    <div class="bar" style="background:var(--navy)"></div>
  </div>
  <div class="service" style="left:209px">
    <svg width="118" height="102" aria-hidden="true"><polygon points="59,0 118,102 0,102" fill="var(--sky)"/>
      <g fill="none" stroke="#fff" stroke-width="2"><path d="M45 66 a9 9 0 0 1 4-17 a11 11 0 0 1 21 0 a9 9 0 0 1 4 17 z"/><path d="M52 66 v12 M59 66 v16 M66 66 v12"/><circle cx="52" cy="80" r="2"/><circle cx="59" cy="84" r="2"/><circle cx="66" cy="80" r="2"/></g></svg>
    <h4>CLOUD SOLUTIONS</h4>
    <p>Sed ut perspiciatis unde omnis iste natus error sit voluptatem accusa ntium doloremque laudantium, totam rem aperiam, eaque ipsa quae ab illo inventore veritatis et quasi architecto beatae vitae dicta sunt explicabo. Nemo enim ipsam voluptatem quia voluptas sit aspernatur aut odit aut fugit, sed quia consequuntu.</p>
    <div class="bar" style="background:var(--sky)"></div>
  </div>
  <div class="service" style="left:403px">
    <svg width="118" height="102" aria-hidden="true"><polygon points="59,0 118,102 0,102" fill="var(--blue)"/>
      <g fill="none" stroke="#fff" stroke-width="2"><circle cx="59" cy="68" r="12"/><rect x="53" y="66" width="12" height="9" fill="#fff"/><path d="M55 66 v-4 a4 4 0 0 1 8 0 v4"/><path d="M41 68 h6 M71 68 h6 M59 50 v6 M59 80 v6 M46 55 l5 5 M72 55 l-5 5 M46 81 l5 -5 M72 81 l-5 -5"/></g></svg>
    <h4>CYBERSECURITY</h4>
    <p>Sed ut perspiciatis unde omnis iste natus error sit voluptatem accusa ntium doloremque laudantium, totam rem aperiam, eaque ipsa quae ab illo inventore veritatis et quasi architecto beatae vitae dicta sunt explicabo. Nemo enim ipsam voluptatem quia voluptas sit aspernatur aut odit aut fugit, sed quia consequuntu.</p>
    <div class="bar" style="background:var(--blue)"></div>
  </div>
  <div class="service" style="left:581px">
    <svg width="118" height="102" aria-hidden="true"><polygon points="59,0 118,102 0,102" fill="var(--ink)"/>
      <g fill="none" stroke="#fff" stroke-width="2.2"><path d="M47 72 v-6 a12 12 0 0 1 24 0 v6"/><rect x="44" y="68" width="6" height="12" rx="2"/><rect x="68" y="68" width="6" height="12" rx="2"/><path d="M71 80 q0 6 -9 6"/></g></svg>
    <h4>SUPPORT</h4>
    <p>Sed ut perspiciatis unde omnis iste natus error sit voluptatem accusa ntium doloremque laudantium, totam rem aperiam, eaque ipsa quae ab illo inventore veritatis et quasi architecto beatae vitae dicta sunt explicabo. Nemo enim ipsam voluptatem quia voluptas sit aspernatur aut odit aut fugit, sed quia consequuntu.</p>
    <div class="bar" style="background:var(--ink)"></div>
  </div>
</section>

<!-- Technology solutions -->
<section class="slide" style="left:55px;top:627px">
  <div class="brand" style="left:22px;top:22px;font-size:21px">VELTRION<span class="brand-mark" style="width:7px;height:7px"></span></div>
  <h2 class="title underlined" style="left:207px;top:17px;font-size:17px;font-weight:500">TECHNOLOGY SOLUTIONS</h2>
  <p class="body" style="left:23px;top:75px;width:690px;font-size:8.8px;line-height:1.3">Sed ut perspiciatis unde omnis iste natus error sit voluptatem accusantium doloremque laudantium, totam rem aperiam, eaque ipsa quae ab illo inventore veritatis et quasi architecto beatae vitae dicta sunt explicabo. Nemo enim ipsam voluptatem quia voluptas sit aspernatur aut odit aut fugit, sed quia consequuntur magni dolores eos qui ratione voluptatem sequi nesciunt. Neque porro quisquam est, qui dolorem ipsum quia dolor sit amet, consectetur, adipisci velit, sed quia non numquam eius modi tempora incidunt ut labore et dolore magnam aliquam quaerat voluptatem.</p>
  <div class="list-box" style="left:23px">
    <h4>HEADING</h4>
    <ul>
      <li>Lorem ipsum dolor sit amet, consectetur adipiscing elit.</li>
      <li>Vivamus non ex egestas, tempus lorem eget, tempus risus.</li>
      <li>Ut commodo ex sit amet elit ultricies, et vestibulum tellus dictum.</li>
      <li>In bibendum libero vitae est varius dignissim.</li>
      <li>Sed viverra velit accumsan tempus lacinia.</li>
      <li>Nam a dui quis ante lobortis posuere eget eget lectus.</li>
      <li>Nam et tellus aliquet, mattis lacus nec, sollicitudin magna.</li>
      <li>Etiam id nulla eu nisl dapibus mollis.</li>
      <li>Integer eu urna maximus, blandit lectus ac, cursus ligula.</li>
    </ul>
  </div>
  <div class="list-box" style="left:373px">
    <h4>HEADING</h4>
    <ul>
      <li>Lorem ipsum dolor sit amet, consectetur adipiscing elit.</li>
      <li>Vivamus non ex egestas, tempus lorem eget, tempus risus.</li>
      <li>Ut commodo ex sit amet elit ultricies, et vestibulum tellus dictum.</li>
      <li>In bibendum libero vitae est varius dignissim.</li>
      <li>Sed viverra velit accumsan tempus lacinia.</li>
      <li>Nam a dui quis ante lobortis posuere eget eget lectus.</li>
      <li>Nam et tellus aliquet, mattis lacus nec, sollicitudin magna.</li>
      <li>Etiam id nulla eu nisl dapibus mollis.</li>
      <li>Integer eu urna maximus, blandit lectus ac, cursus ligula.</li>
    </ul>
  </div>
  <div class="abs" style="left:0;top:408px;width:247px;height:10px;background:var(--navy)"></div>
  <div class="abs" style="left:247px;top:408px;width:250px;height:10px;background:var(--sky)"></div>
  <div class="abs" style="left:497px;top:408px;width:248px;height:10px;background:var(--blue)"></div>
</section>

<!-- Chart -->
<section class="slide" style="left:514px;top:627px">
  <svg class="abs" style="left:0;top:0" width="745" height="418" aria-hidden="true">
    <polygon points="310,0 745,0 745,418 388,418" fill="var(--ice)"/>
    <polygon points="295,0 310,0 388,418 373,418" fill="var(--navy)"/>
  </svg>
  <div class="brand" style="left:36px;top:45px;font-size:21px">VELTRION<span class="brand-mark" style="width:7px;height:7px"></span></div>
  <h2 class="title" style="left:371px;top:24px;font-size:17px;font-weight:500;line-height:1.65">LOREM IPSUM DOLOR SIT AMET<br>CONSECTETUR ADIPISCING</h2>
  <div class="abs" style="left:373px;top:96px;width:126px;height:2px;background:var(--sky)"></div>
  <svg class="abs" style="left:20px;top:128px" width="467" height="265" aria-label="Line chart rising over eleven periods">
    <rect width="467" height="265" fill="#fff"/>
    <g fill="#f5f8fc">
      <rect x="25" y="28" width="40" height="195"/><rect x="102" y="28" width="38" height="195"/><rect x="178" y="28" width="38" height="195"/><rect x="255" y="28" width="38" height="195"/><rect x="332" y="28" width="38" height="195"/><rect x="408" y="28" width="42" height="195"/>
    </g>
    <g font-family="Questrial" font-size="9" fill="#555" text-anchor="end">
      <text x="16" y="38">10</text><text x="16" y="58">09</text><text x="16" y="78">08</text><text x="16" y="98">07</text><text x="16" y="118">06</text><text x="16" y="138">05</text><text x="16" y="158">04</text><text x="16" y="178">03</text><text x="16" y="198">02</text><text x="16" y="218">01</text>
    </g>
    <g font-family="Questrial" font-size="9" fill="#555" text-anchor="middle">
      <text x="45" y="241">01</text><text x="83" y="241">02</text><text x="121" y="241">03</text><text x="160" y="241">04</text><text x="198" y="241">05</text><text x="237" y="241">06</text><text x="275" y="241">07</text><text x="314" y="241">08</text><text x="352" y="241">09</text><text x="391" y="241">10</text><text x="429" y="241">11</text>
    </g>
    <defs><linearGradient id="chartFill" x1="0" y1="0" x2="0" y2="1"><stop offset="0" stop-color="#7BADD7" stop-opacity=".55"/><stop offset="1" stop-color="#E8F1F8" stop-opacity=".4"/></linearGradient></defs>
    <path d="M25 195 C35 175 45 180 55 192 S70 155 80 170 S95 140 105 150 S115 165 125 150 S140 140 145 155 S160 140 170 148 S185 145 195 145 S210 120 217 140 S230 130 237 132 S245 165 255 160 S265 135 275 145 S290 130 300 140 S310 110 320 118 S335 90 342 105 S355 80 362 90 S378 70 385 80 S400 60 408 70 S420 50 428 35 S440 20 448 20 L448 223 L25 223 Z" fill="url(#chartFill)"/>
    <path d="M25 195 C35 175 45 180 55 192 S70 155 80 170 S95 140 105 150 S115 165 125 150 S140 140 145 155 S160 140 170 148 S185 145 195 145 S210 120 217 140 S230 130 237 132 S245 165 255 160 S265 135 275 145 S290 130 300 140 S310 110 320 118 S335 90 342 105 S355 80 362 90 S378 70 385 80 S400 60 408 70 S420 50 428 35 S440 20 448 20" fill="none" stroke="var(--blue)" stroke-width="1.8"/>
    <circle cx="237" cy="132" r="11" fill="var(--mist)" opacity=".8"/>
    <circle cx="237" cy="132" r="6" fill="var(--ink)"/>
  </svg>
  <p class="body" style="left:512px;top:146px;width:202px;line-height:1.45">Sed ut perspiciatis unde omnis iste natus error sit voluptatem accusantium doloremque laudantium, totam rem aperiam, eaque ipsa quae ab illo inventore veritatis et quasi architecto beatae vitae dicta sunt explicabo. Nemo enim ipsam voluptatem quia voluptas sit aspernatur aut odit aut fugit, sed quia consequuntur magni dolores eos qui ratione voluptatem sequi nesciunt. Neque porro quisquam est, qui dolorem ipsum quia dolor sit amet, consectetur, adipisci velit, sed quia non numquam eius modi tempora incidunt ut labore et dolore magnam aliquam quaerat voluptatem.</p>
</section>

<!-- Infodata process -->
<section class="slide" style="left:53px;top:906px">
  <div class="brand" style="left:25px;top:25px;font-size:21px">VELTRION<span class="brand-mark" style="width:7px;height:7px"></span></div>
  <h2 class="title" style="left:217px;top:18px;font-size:17px;font-weight:500">HEADING GOES HERE</h2>
  <svg class="abs" style="left:0;top:0" width="745" height="418" aria-hidden="true">
    <g fill="none" stroke="var(--sky)" stroke-width="1.8">
      <path d="M28 226 A70 70 0 0 1 167 226"/>
      <path d="M167 226 A69 69 0 0 0 305 226"/>
      <path d="M305 226 A69 69 0 0 1 444 226"/>
      <path d="M444 226 A69 69 0 0 0 583 226"/>
      <path d="M583 226 A70 70 0 0 1 722 226"/>
    </g>
    <g fill="var(--sky)"><circle cx="28" cy="226" r="4"/><circle cx="722" cy="226" r="4"/></g>
    <g fill="var(--navy)"><circle cx="97" cy="156" r="4"/><circle cx="236" cy="295" r="4"/><circle cx="375" cy="157" r="4"/><circle cx="507" cy="294" r="4"/><circle cx="653" cy="156" r="4"/></g>
    <g fill="none" stroke="var(--blue)" stroke-width="2"><circle cx="97" cy="226" r="50"/><circle cx="236" cy="226" r="50"/><circle cx="375" cy="226" r="50"/><circle cx="514" cy="226" r="50"/><circle cx="653" cy="226" r="50"/></g>
    <g fill="var(--blue)"><circle cx="97" cy="226" r="42"/><circle cx="236" cy="226" r="42"/><circle cx="375" cy="226" r="42"/><circle cx="514" cy="226" r="42"/><circle cx="653" cy="226" r="42"/></g>
    <g fill="none" stroke="#fff" stroke-width="1.6">
      <circle cx="97" cy="226" r="16"/><circle cx="97" cy="226" r="10"/><circle cx="97" cy="226" r="4"/><path d="M97 226 l14 -14 M108 209 l3 3 l3 -3"/>
      <path d="M222 222 a9 7 0 1 1 4 8 l-6 3 l2 -5 z"/><path d="M238 216 a10 8 0 1 1 6 12 l4 5 l-8 -3"/>
      <path d="M360 238 h30 M362 238 v-8 h5 v8 M370 238 v-12 h5 v12 M378 238 v-16 h5 v16 M360 224 l10 -6 l8 3 l10 -9"/>
      <path d="M503 210 h20 v26 a4 4 0 0 1 -4 4 h-20 a4 4 0 0 0 4 -4 z M507 218 h12 M507 224 h12 M507 230 h10"/>
      <rect x="638" y="212" width="30" height="20" rx="2"/><path d="M653 232 v6 M645 240 h16"/>
    </g>
  </svg>
  <div class="info" style="left:37px;top:280px"><h4>INFODATA 01</h4><div class="tick"></div><p>Lorem ipsum dolor sit amet, consectetuer adipiscing elit, sed diam nonummy nibh euismod tincidunt ut laoreet dolore magna aliquam erat.</p></div>
  <div class="info" style="left:176px;top:99px"><h4>INFODATA 02</h4><div class="tick"></div><p>Lorem ipsum dolor sit amet, consectetuer adipiscing elit, sed diam nonummy nibh euismod tincidunt ut laoreet dolore magna aliquam erat.</p></div>
  <div class="info" style="left:315px;top:283px"><h4>INFODATA 03</h4><div class="tick"></div><p>Lorem ipsum dolor sit amet, consectetuer adipiscing elit, sed diam nonummy nibh euismod tincidunt ut laoreet dolore magna aliquam erat.</p></div>
  <div class="info" style="left:454px;top:99px"><h4>INFODATA 04</h4><div class="tick"></div><p>Lorem ipsum dolor sit amet, consectetuer adipiscing elit, sed diam nonummy nibh euismod tincidunt ut laoreet dolore magna aliquam erat.</p></div>
  <div class="info" style="left:593px;top:283px"><h4>INFODATA 05</h4><div class="tick"></div><p>Lorem ipsum dolor sit amet, consectetuer adipiscing elit, sed diam nonummy nibh euismod tincidunt ut laoreet dolore magna aliquam erat.</p></div>
</section>

<!-- Closing -->
<section class="slide" style="left:514px;top:904px">
  <div class="abs" style="left:0;top:0;width:745px;height:418px;background:linear-gradient(120deg,#f4f8fc 0%,#E8F1F8 45%,#f2f6fa 100%)" role="img" aria-label="Faded office photo of two colleagues working at a laptop"></div>
  <div class="abs" style="left:0;top:152px;width:745px;text-align:center;font-family:'Poppins',sans-serif;font-weight:700;font-size:20px;color:var(--ink);letter-spacing:1.5px">VELTRION<span class="brand-mark" style="width:8px;height:8px"></span></div>
  <h1 class="abs thanks">THANK YOU</h1>
  <svg class="abs" style="left:0;top:0" width="745" height="418" aria-hidden="true">
    <line x1="372" y1="330" x2="372" y2="418" stroke="var(--blue)" stroke-width="2"/>
    <polygon points="45,340 90,418 0,418" fill="var(--sky)"/>
    <path d="M34 382 c-3 3 -2 9 4 16 c6 6 12 8 15 5 l2 -3 l-5 -4 l-3 2 c-3 -1 -8 -6 -9 -9 l2 -3 l-4 -5 z" fill="#fff"/>
    <polygon points="700,338 745,418 655,418" fill="var(--navy)"/>
    <rect x="690" y="385" width="18" height="12" fill="#fff"/>
    <path d="M690 385 l9 7 l9 -7" fill="none" stroke="var(--navy)" stroke-width="1.5"/>
  </svg>
  <div class="abs contact" style="left:90px;top:365px"><h4>CALL US</h4><p>+1 555 010 0199</p></div>
  <div class="abs contact" style="left:521px;top:365px"><h4>EMAIL US</h4><p>info@veltrion.com</p></div>
</section>

</body>
</html>
```